Business cards for Norwegian software consultancy business

We are in need of business cards for our Norwegian consultancy company.
“Valto Brindex AS” specializes in software development, architecture and agile methodology, providing mostly on-site services at customers.
The cards should reflect a certain level of business professionalism with an elegant touch, while paying tribute to our modern and technological heritage. Our logo should be featured, as well as room for basic information about the cardholder and legal information of the company (company name, address and VAT number).
We would like our cards to reflect that we are a modern consulting company. It should present a professional image that people will remember. The texture and color pallette should reflect our professionalism and reliability, so we prefer a light color pallette with colors such as gray, white, blue and black. The number of colors used should however not be overwhelming, with the text being distinct and readable.
We are open to untraditional layouts and playful designs as long as they communicate the intent stated above.
You could also take a look at our website http://www.brindex.no for input on our visual profile.
Our logo is attached in the form of vectors and rasterized PNG. Please comment if you would like the black-white and/or inverted versions as well.
Industry/Entity Type
Architecture
Contact Information for Business Card
Company information:
Valto Brindex AS
Kvernlia 14, 3170 Sem
482 71 519
info@brindex.no
www.brindex.no
Employee information:
Full name
Title
Email
Phone
Font styles to use
Look and feel

```html
<!DOCTYPE html>
<html lang="en">
<head>
<meta charset="utf-8">
<title>Valto Brindex AS – Business Cards</title>
<link href="https://fonts.googleapis.com/css2?family=Roboto:wght@300;400;700&family=Roboto+Condensed:wght@400&display=swap" rel="stylesheet">
<style>
  :root {
    --bg-top: #8a9694;
    --bg-bottom: #2b3232;
    --card-black: #060606;
    --card-gray: #a3a3a3;
    --watermark: #2a2a2a;
    --tagline: #6f6f6f;
    --white: #ffffff;
    --accent-blue: #6fa7d6;
  }
  * { margin: 0; padding: 0; box-sizing: border-box; }
  html, body { width: 1200px; height: 900px; overflow: hidden; }
  body {
    position: relative;
    background: radial-gradient(ellipse at 45% 35%, var(--bg-top) 0%, #5c6766 55%, var(--bg-bottom) 100%);
    font-family: "Roboto", Arial, sans-serif;
  }
  .card {
    position: absolute;
    width: 540px;
    height: 310px;
    border-radius: 34px 8px 34px 8px;
    overflow: hidden;
    background: var(--card-gray);
    box-shadow: 0 14px 30px rgba(0, 0, 0, 0.35);
  }

  /* Contact side */
  .card--front { left: 610px; top: 90px; }
  .card--front .band {
    position: absolute; left: 0; top: 0; width: 100%; height: 108px;
    background: var(--card-black);
  }
  .brand {
    position: absolute; left: 38px; top: 38px;
    display: flex; align-items: center; gap: 14px;
  }
  .brand__square { width: 30px; height: 30px; background: var(--accent-blue); }
  .brand__name {
    color: var(--white); font-weight: 300; font-size: 30px;
    letter-spacing: 4px; text-transform: uppercase; line-height: 1;
  }
  .contact {
    position: absolute; left: 340px; top: 122px;
    color: var(--white); font-size: 15px; line-height: 1.3;
  }
  .contact__name { font-weight: 300; font-size: 17px; }
  .contact__title { font-weight: 700; font-size: 17px; margin-bottom: 8px; }
  .contact__line { display: flex; align-items: center; gap: 7px; font-weight: 300; }
  .contact__line svg { width: 13px; height: 13px; flex: none; }
  .contact__address { font-weight: 700; font-size: 13px; margin-left: 20px; margin-top: 4px; line-height: 1.45; }

  /* Tagline side */
  .card--back { left: 80px; top: 470px; }
  .card--back .band {
    position: absolute; left: 0; top: 0; width: 100%; height: 212px;
    background: var(--card-black);
  }
  .watermark-name {
    position: absolute; right: 40px; top: 60px;
    color: var(--watermark); font-weight: 300; font-size: 44px;
    letter-spacing: 5px; text-transform: uppercase; line-height: 1;
  }
  .tagline {
    position: absolute; right: 40px; top: 228px;
    text-align: right;
    font-family: "Roboto Condensed", "Arial Narrow", sans-serif;
    color: var(--tagline); font-size: 14px; letter-spacing: 0.5px;
    text-transform: uppercase; line-height: 1.25;
  }
</style>
</head>
<body>
  <section class="card card--front" aria-label="Business card, contact side">
    <div class="band"></div>
    <div class="brand">
      <span class="brand__square"></span>
      <span class="brand__name">Valto Brindex</span>
    </div>
    <div class="contact">
      <p class="contact__name">Sindre Halvorsen</p>
      <p class="contact__title">Co-Founder &amp; CEO</p>
      <p class="contact__line">
        <svg viewBox="0 0 13 13" aria-hidden="true"><rect x="3" y="0.5" width="7" height="12" rx="1.2" fill="none" stroke="#fff" stroke-width="1.2"/><line x1="5.5" y1="10.5" x2="7.5" y2="10.5" stroke="#fff"/></svg>
        (047) 512-3980
      </p>
      <p class="contact__line">
        <svg viewBox="0 0 13 13" aria-hidden="true"><rect x="0.6" y="2.5" width="11.8" height="8" fill="none" stroke="#fff" stroke-width="1.2"/><polyline points="0.6,2.5 6.5,7 12.4,2.5" fill="none" stroke="#fff" stroke-width="1.2"/></svg>
        info@brindex.no
      </p>
      <p class="contact__line">
        <svg viewBox="0 0 13 13" aria-hidden="true"><circle cx="6.5" cy="6.5" r="5.8" fill="none" stroke="#fff" stroke-width="1.1"/><ellipse cx="6.5" cy="6.5" rx="2.6" ry="5.8" fill="none" stroke="#fff" stroke-width="1"/><line x1="0.7" y1="6.5" x2="12.3" y2="6.5" stroke="#fff"/></svg>
        brindex.no
      </p>
      <p class="contact__address">Kvernlia 14<br>3170 Sem</p>
    </div>
  </section>

  <section class="card card--back" aria-label="Business card, tagline side">
    <div class="band"></div>
    <span class="watermark-name">Valto Brindex</span>
    <p class="tagline">Rental of qualified resources in software development<br>Project management and IT operations</p>
  </section>
</body>
</html>
```